A design led business card for the construction industry

High-end business card to match logo. White logo on dark grey/off black to the front. Matching dark font on white to back, possibly with logo design again.

We offer construction and project management services to commercial and private clients in the UK. Projetcs range from newbuilds, conversion of listed buildings and refurbishments and extensions of existing homes. Our focus is on quality and attention to detail using the highest skills.

Contact Information for Business Card

Name; Dorian Keble BSc
Position; Project Manager
Mobile; 07962 408 175
Tel; 01632 960457
email; dorian@stonevale.co.uk
web; www.stonevale.co.uk
Address; Ashcombe Vale, KX4 7PW

Colors

Designer to choose only greyscale colors for use in the design.

Requirements
Must have
• To include the below description of the business,

CONSTRUCTION - PROJECT MANAGEMENT
Nice to have
• The posibility of the top back of the card being used as a ruler. So will have a measurement to scale in mm or an architect scale of 1:50
Should not have
• Should not be portrait

```html
<!DOCTYPE html>
<html lang="en">
<head>
<meta charset="utf-8">
<title>Stonevale – Business Card</title>
<link href="https://fonts.googleapis.com/css2?family=Arimo:wght@400;700&family=Montserrat:wght@400&display=swap" rel="stylesheet">
<style>
  :root {
    --backdrop: #b9b9b9;
    --card-dark: #262626;
    --card-light: #ffffff;
    --ink: #111111;
    --ink-soft: #222222;
    --rule: #9a9a9a;
    --paper-text: #ffffff;
  }
  * { margin: 0; padding: 0; box-sizing: border-box; }
  html, body {
    width: 1200px; height: 1200px; overflow: hidden;
    background: var(--backdrop);
  }
  .stage { position: relative; width: 1200px; height: 1200px; }

  .card {
    position: absolute; top: 303px; width: 368px; height: 594px;
  }
  .card--front { left: 201px; background: var(--card-dark); color: var(--paper-text); }
  .card--back { left: 599px; width: 364px; background: var(--card-light); color: var(--ink); }

  .centered { position: absolute; left: 0; right: 0; text-align: center; }

  .wordmark {
    font-family: "Montserrat", sans-serif; font-weight: 400;
    letter-spacing: 0.62em; text-indent: 0.62em; white-space: nowrap;
  }
  .card--front .wordmark { top: 489px; font-size: 25px; }
  .tagline {
    top: 538px; font-family: "Arimo", sans-serif; font-size: 14px; letter-spacing: 0.01em;
  }

  .brand-square {
    position: absolute; left: 132px; top: 88px; width: 100px; height: 100px;
    border: 4px solid var(--ink); border-radius: 3px;
  }
  .card--back .wordmark { top: 226px; font-size: 25px; color: var(--ink); }

  .contact { font-family: "Arimo", sans-serif; color: var(--ink-soft); }
  .person-name { top: 330px; font-size: 19px; }
  .person-name strong { font-weight: 700; color: var(--ink); }
  .person-name .post-nominal { font-size: 17px; }
  .person-role { top: 352px; font-size: 17px; }

  .icon-row {
    position: absolute; top: 386px; left: 86px; width: 192px; height: 26px;
    display: flex; align-items: center; justify-content: center; gap: 4px;
  }
  .icon-row .rule { flex: 1; height: 1px; background: var(--rule); }
  .icon-row .rule:first-child { margin-right: 4px; }
  .icon-row .rule:last-child { margin-left: 4px; }
  .icon { width: 25px; height: 25px; display: block; }

  .details { top: 426px; font-size: 17px; line-height: 21.5px; }
  .divider { position: absolute; top: 521px; left: 89px; width: 194px; height: 1px; background: var(--rule); }
  .address { top: 533px; font-size: 17px; }
</style>
</head>
<body>
<main class="stage">

  <section class="card card--front" aria-label="Card front">
    <p class="centered wordmark">STONEVALE</p>
    <p class="centered tagline">CONSTRUCTION - PROJECT MANAGEMENT</p>
  </section>

  <section class="card card--back" aria-label="Card back">
    <div class="brand-square" aria-hidden="true"></div>
    <p class="centered wordmark">STONEVALE</p>

    <p class="centered contact person-name"><strong>DORIAN KEBLE</strong> <span class="post-nominal">BSc</span></p>
    <p class="centered contact person-role">Project Manager</p>

    <div class="icon-row" aria-hidden="true">
      <span class="rule"></span>
      <svg class="icon" viewBox="0 0 25 25">
        <rect width="25" height="25" rx="4" fill="#111"/>
        <rect x="8.5" y="5" width="8" height="14" rx="1.2" fill="none" stroke="#fff" stroke-width="1.5"/>
        <circle cx="12.5" cy="17" r="0.9" fill="#fff"/>
      </svg>
      <svg class="icon" viewBox="0 0 25 25">
        <rect width="25" height="25" rx="4" fill="#111"/>
        <path d="M5 10 Q12.5 4 20 10 L18 12 L16 10 L9 10 L7 12 Z" fill="#fff"/>
        <path d="M8 12 L17 12 L19 19 L6 19 Z" fill="#fff"/>
        <circle cx="12.5" cy="15.5" r="1.8" fill="#111"/>
      </svg>
      <svg class="icon" viewBox="0 0 25 25">
        <rect width="25" height="25" rx="4" fill="#111"/>
        <rect x="5" y="7.5" width="15" height="10" fill="none" stroke="#fff" stroke-width="1.3"/>
        <path d="M5 7.5 L12.5 13.5 L20 7.5 M5 17.5 L10.5 12 M20 17.5 L14.5 12" fill="none" stroke="#fff" stroke-width="1.1"/>
      </svg>
      <svg class="icon" viewBox="0 0 25 25">
        <rect width="25" height="25" rx="4" fill="#111"/>
        <circle cx="12.5" cy="12.5" r="7" fill="#fff"/>
        <ellipse cx="12.5" cy="12.5" rx="3" ry="7" fill="none" stroke="#111" stroke-width="1"/>
        <path d="M5.5 12.5 H19.5" stroke="#111" stroke-width="1"/>
      </svg>
      <span class="rule"></span>
    </div>

    <p class="centered contact details">
      07962 408 175<br>
      01632 960457<br>
      dorian@stonevale.co.uk<br>
      www.stonevale.co.uk
    </p>
    <div class="divider"></div>
    <p class="centered contact address">Ashcombe Vale, KX4 7PW</p>
  </section>

</main>
</body>
</html>
```